CANNABIS BASED BUSINESS CARD DESIGN AND CREATION

WE ARE A PRIVATELY OWNED INVESTMENT CORPORATION. WE PRIMARILY INVEST IN LEGAL PUBLICALLY TRADED CANNABIS COMPANIES THAT ARE TRADED THROUGH THE OTC OR VOLTRIX. WE OFFER THE PUBLIC AN OPPORTUNITY TO PARTICIPATE DIRECTLY WITH THESE COMPANIES FOR NO FEES, NO COMMISSIONS AND IN DEPTH RESEARCH ON EVERY COMPANY PROFILE. WE ARE ALSO PRO FEDERAL LEGALIZATION AND WILL APPLY FOR CULTIVATION AND DISPENSARY LICENSES WHEN THEY BECOME AVAILABLE.

Target Market(s)

30-60 FEMALE AND MALE INVESTORS

Industry/Entity Type

Business

Contact Information for Business Card

EDS CAPITAL GROUP CORPERIN D SLAUGHTER(469) 426-6302ERIN@EDSCAPITALGROUP.COM

Font styles to use
Decorative

Requirements
Must have
• COMPANY LOGO
• CANNABIS LOGO
Nice to have
• MODERN FONT AND LOGOS

```html
<!DOCTYPE html>
<html lang="en">
<head>
<meta charset="utf-8">
<title>TQM Capital Group Corp – Business Card</title>
<link href="https://fonts.googleapis.com/css2?family=Lato:wght@400;700&display=swap" rel="stylesheet">
<style>
  :root {
    --backdrop: #6f7d1a;
    --card: #0b0b0b;
    --leaf-green: #2fb34c;
    --watermark: #2a2a2a;
    --accent-red: #e0262c;
    --text-light: #e6e6e6;
    --rule: #2e2e2e;
  }
  * { margin: 0; padding: 0; box-sizing: border-box; }
  html, body { width: 1200px; height: 900px; overflow: hidden; }
  body {
    background: var(--backdrop);
    font-family: "Lato", Arial, sans-serif;
    position: relative;
  }
  .card {
    position: absolute;
    width: 540px;
    height: 320px;
    border-radius: 22px;
    background: linear-gradient(150deg, #1e1e1e 0%, var(--card) 55%, #050505 100%);
    box-shadow: 0 10px 24px rgba(0,0,0,0.35);
    overflow: hidden;
  }
  .card-front { left: 90px; top: 110px; }
  .card-back { left: 570px; top: 470px; }

  .leaf-watermark {
    position: absolute;
    left: 290px;
    top: 10px;
    width: 280px;
    height: 280px;
    border-radius: 50%;
    background: radial-gradient(circle at 50% 50%, var(--watermark) 0%, rgba(38,38,38,0.7) 40%, rgba(11,11,11,0) 72%);
  }

  .brand {
    position: absolute;
    display: flex;
    align-items: center;
    gap: 14px;
    color: var(--leaf-green);
    font-weight: 700;
    letter-spacing: 0.08em;
  }
  .brand-mark {
    border-radius: 50%;
    background: var(--leaf-green);
    flex: none;
  }
  .brand-name { display: flex; flex-direction: column; line-height: 1.15; white-space: nowrap; }

  .card-front .brand { left: 150px; top: 102px; font-size: 30px; }
  .card-front .brand-mark { width: 34px; height: 34px; }

  .card-back .brand { right: 40px; top: 30px; font-size: 17px; gap: 10px; }
  .card-back .brand-mark { width: 20px; height: 20px; }

  .divider {
    position: absolute;
    height: 1px;
    background: var(--rule);
  }
  .divider-contact { right: 30px; top: 112px; width: 250px; }
  .divider-name { left: 30px; top: 262px; width: 230px; }

  .contact-list {
    position: absolute;
    right: 30px;
    top: 128px;
    width: 250px;
    list-style: none;
  }
  .contact-item {
    display: flex;
    align-items: center;
    gap: 9px;
    color: var(--text-light);
    font-size: 12px;
    line-height: 22px;
    white-space: nowrap;
  }
  .contact-icon { width: 12px; height: 12px; flex: none; }

  .person-name {
    position: absolute;
    left: 30px;
    top: 236px;
    color: var(--accent-red);
    font-size: 17px;
    font-weight: 400;
    letter-spacing: 0.02em;
  }
</style>
</head>
<body>

  <section class="card card-front" aria-label="Card front">
    <div class="leaf-watermark" role="img" aria-label="Faint cannabis leaf watermark"></div>
    <div class="brand">
      <span class="brand-mark"></span>
      <span class="brand-name"><span>TQM CAPITAL</span><span>GROUP CORP</span></span>
    </div>
  </section>

  <section class="card card-back" aria-label="Card back">
    <div class="brand">
      <span class="brand-mark"></span>
      <span class="brand-name"><span>TQM CAPITAL</span><span>GROUP CORP</span></span>
    </div>
    <div class="divider divider-contact"></div>
    <ul class="contact-list">
      <li class="contact-item">
        <svg class="contact-icon" viewBox="0 0 12 12" aria-hidden="true">
          <path d="M2.5 1 L4.5 1 L5 3.5 L3.8 4.5 Q5 7 7.5 8.2 L8.5 7 L11 7.5 L11 9.5 Q11 11 9.5 11 Q1 10 1 2.5 Q1 1 2.5 1 Z" fill="var(--leaf-green)"/>
        </svg>
        <span>(555) 013-4478</span>
      </li>
      <li class="contact-item">
        <svg class="contact-icon" viewBox="0 0 12 12" aria-hidden="true">
          <rect x="0.5" y="2" width="11" height="8" fill="var(--leaf-green)"/>
          <path d="M0.5 2 L6 6.5 L11.5 2" fill="none" stroke="#0b0b0b" stroke-width="1"/>
        </svg>
        <span>marla@tqmcapitalgroup-demo.com</span>
      </li>
      <li class="contact-item">
        <svg class="contact-icon" viewBox="0 0 12 12" aria-hidden="true">
          <rect x="1" y="5" width="6" height="3.5" rx="1.75" fill="none" stroke="var(--leaf-green)" stroke-width="1.4" transform="rotate(-45 4 6.75)"/>
          <rect x="5" y="3.5" width="6" height="3.5" rx="1.75" fill="none" stroke="var(--leaf-green)" stroke-width="1.4" transform="rotate(-45 8 5.25)"/>
        </svg>
        <span>www.tqmcapitalgroup-demo.com</span>
      </li>
    </ul>
    <p class="person-name">MARLA J PENDLEBURY</p>
    <div class="divider divider-name"></div>
  </section>

</body>
</html>
```